Storm Restoration Contractor needs a professional letterhead design

Looking for a professional letterhead design. Not looking for your cheapo MS Word standard ones that are readily available. Dont want it to be cookie cutter look like ones readily available online. We just recently changed our logo and want to freshen up all our documents. Our company handles restoring a property back to a pre-loss condition after a storm damages it. For example, wind, hail, flood, fire losses.

Target Market(s)

Property Owners, Homeowners, Property Owners, Commercial Property Owners, Property Management Companies

Industry/Entity Type

Construction Company

Requirements
Must have
• Professional, Use 1 of 2 logo options
• Storm Restoration, Roofing, Siding, Windows

```html
<!DOCTYPE html>
<html lang="en">
<head>
<meta charset="utf-8">
<title>Stormline Exteriors Letterhead</title>
<link rel="stylesheet" href="https://fonts.googleapis.com/css2?family=Open+Sans:wght@400;600;700&display=swap">
<style>
  :root {
    --backdrop: #8b8680;
    --paper: #ffffff;
    --brand-blue: #1f74c1;
    --brand-grey: #55595e;
    --ink: #4a4d52;
    --ink-dark: #2a2c30;
  }
  * { box-sizing: border-box; margin: 0; padding: 0; }
  html, body {
    width: 1200px; height: 795px; overflow: hidden;
    background: var(--backdrop);
    font-family: "Open Sans", Arial, sans-serif;
  }
  .letterhead {
    position: absolute; left: 330px; top: 15px;
    width: 540px; height: 764px;
    background: var(--paper);
    box-shadow: 0 6px 18px rgba(0,0,0,.25);
    overflow: hidden;
  }
  .brand {
    position: absolute; left: 42px; top: 48px;
    display: flex; align-items: center; gap: 10px;
  }
  .brand-dot {
    width: 30px; height: 30px; border-radius: 50%;
    border: 3px solid var(--brand-blue);
  }
  .brand-name {
    font-weight: 700; font-size: 19px; line-height: 1.05;
    color: var(--brand-blue); letter-spacing: .5px; text-transform: uppercase;
  }
  .contact {
    position: absolute; right: 40px; top: 40px;
    list-style: none; text-align: right;
    font-size: 8.5px; line-height: 1.55; color: var(--ink-dark);
  }
  .contact li { display: flex; justify-content: flex-end; align-items: center; gap: 5px; }
  .contact .icon { width: 9px; height: 9px; }
  .letter {
    position: absolute; left: 42px; top: 200px; width: 400px;
    font-size: 9.5px; line-height: 1.5; color: var(--ink);
  }
  .salutation { font-weight: 700; font-size: 11px; color: var(--ink-dark); margin-bottom: 10px; }
  .letter p { margin-bottom: 10px; }
  .signature {
    display: block; width: 90px; height: 34px; margin-top: 16px;
    background: linear-gradient(90deg, #e9eaec, #f4f4f5);
    border-radius: 3px;
  }
  .footer-wave { position: absolute; left: 0; bottom: 0; width: 540px; height: 200px; }
  .footer-url { font-size: 10px; fill: #fff; font-family: "Open Sans", Arial, sans-serif; }
</style>
</head>
<body>
  <main class="letterhead">
    <header class="brand">
      <span class="brand-dot"></span>
      <span class="brand-name">Stormline<br>Exteriors</span>
    </header>

    <ul class="contact">
      <li>2280 Harbor Loop,</li>
      <li>Fairview, CA 90210
        <svg class="icon" viewBox="0 0 10 10"><circle cx="5" cy="5" r="5" fill="var(--brand-blue)"/><path d="M5 2.2a2 2 0 0 0-2 2c0 1.5 2 3.6 2 3.6s2-2.1 2-3.6a2 2 0 0 0-2-2z" fill="#fff"/></svg></li>
      <li>(555) 214-3380
        <svg class="icon" viewBox="0 0 10 10"><circle cx="5" cy="5" r="5" fill="var(--brand-blue)"/><path d="M3.2 2.5l1 .2.4 1.3-.6.5a3.5 3.5 0 0 0 1.5 1.5l.5-.6 1.3.4.2 1-.8.6C4.6 7.3 2.7 5.4 2.6 3.3z" fill="#fff"/></svg></li>
      <li>(555) 214-3381
        <svg class="icon" viewBox="0 0 10 10"><circle cx="5" cy="5" r="5" fill="var(--brand-blue)"/><rect x="2.6" y="3.3" width="4.8" height="3.4" fill="#fff"/></svg></li>
      <li>info@stormlineexteriors.com</li>
    </ul>

    <section class="letter">
      <p class="salutation">Dear Mr. Carter,</p>
      <p>Lorem Ipsum is simply dummy text of the printing and typesetting industry. Lorem Ipsum has been the industry's standard dummy text ever since the 1500s, when an unknown printer took a galley of type and scrambled it to make a type specimen book. It has survived not only five centuries, but also the leap into electronic typesetting, remaining essentially unchanged.</p>
      <p>The standard chunk of Lorem Ipsum used since the 1500s is reproduced below for those interested. Sections 1.10.32 and 1.10.33 from "de Finibus Bonorum et Malorum" by Cicero are also reproduced in their exact original form, accompanied by English versions from the 1914 translation by H. Rackham.</p>
      <p>Lorem Ipsum is simply dummy text of the printing and typesetting industry. Lorem Ipsum has been the industry's standard dummy text ever since the 1500s, when an unknown printer took a galley of type and scrambled it to make a type specimen book. It has survived not only five centuries, but also the leap into electronic typesetting, remaining essentially unchanged. It was popularised in the</p>
      <span class="signature" role="img" aria-label="Handwritten signature of the sender"></span>
    </section>

    <svg class="footer-wave" viewBox="0 0 540 200" aria-hidden="true">
      <path d="M0 200 L0 188 C190 186 400 146 540 44 L540 200 Z" fill="var(--brand-blue)"/>
      <path d="M0 181 C185 179 390 136 540 30" fill="none" stroke="var(--brand-grey)" stroke-width="5"/>
      <path d="M0 174 C180 172 380 126 540 18" fill="none" stroke="var(--brand-blue)" stroke-width="3"/>
      <text class="footer-url" x="522" y="186" text-anchor="end">www.stormlineexteriors.com</text>
    </svg>
  </main>
</body>
</html>
```